TeaLantern Flyer

I require an A5 sized flyer to be designed that advertised the new flexible workspace of TeaLantern.
should say it is a "Flexible Workspace with EV Charging"
web address is www.tealantern.co.uk
It should show the 3 different types of membership as priced on the website

```html
<!DOCTYPE html>
<html lang="en">
<head>
<meta charset="utf-8">
<title>TeaLantern Flyer</title>
<link rel="stylesheet" href="https://fonts.googleapis.com/css2?family=Poppins:ital,wght@0,400;0,600;0,700;1,400&display=swap">
<style>
  :root {
    --backdrop: #6e6e6e;
    --dark: #333333;
    --orange: #f39021;
    --blue: #29a9e1;
    --blue-deep: #1c84b8;
    --ink: #2b2b2b;
    --white: #ffffff;
  }
  * { box-sizing: border-box; margin: 0; padding: 0; }
  html, body { width: 1200px; height: 1200px; overflow: hidden; }
  body { background: var(--backdrop); font-family: "Poppins", sans-serif; position: relative; }

  .flyer {
    position: absolute; left: 266px; top: 125px; width: 669px; height: 949px;
    overflow: hidden; background: var(--dark);
  }
  .top-area {
    position: absolute; left: 0; top: 0; width: 100%; height: 291px;
    background: linear-gradient(180deg, #fafafa 0%, #ececec 100%);
  }
  .dark-area {
    position: absolute; left: 0; top: 291px; width: 100%; height: 658px;
    background: radial-gradient(ellipse at 50% 45%, #4a4a4a 0%, #363636 55%, #2e2e2e 100%);
  }
  .accent-band {
    position: absolute; left: 0; top: 273px; width: 100%; height: 9px; background: var(--orange);
  }
  .brand {
    position: absolute; left: 0; top: 22px; width: 100%; text-align: center;
    font-weight: 700; font-size: 46px; color: var(--ink); letter-spacing: -0.5px;
  }
  .hero-frame {
    position: absolute; left: 44px; top: 102px; width: 595px; height: 268px;
    transform: skewX(-7deg); border: 7px solid var(--orange); border-radius: 30px;
    background: linear-gradient(110deg, #dfeaf4 0%, #c9dcec 40%, #9fbf7a 58%, #d8e6f1 70%, #b9cfe2 100%);
  }
  .headline {
    position: absolute; left: 0; top: 388px; width: 100%; text-align: center;
    color: var(--white); font-weight: 700; font-size: 34.5px; line-height: 1.2;
  }
  .headline-accent {
    position: absolute; left: 0; top: 421px; width: 100%; text-align: center;
    color: var(--orange); font-weight: 700; font-size: 52px; line-height: 1.2;
  }

  .plan {
    position: absolute; width: 169px; border-radius: 8px;
    background: linear-gradient(115deg, #ffffff 60%, #f0f0f0 60%);
    box-shadow: 0 18px 16px -12px rgba(0,0,0,.6);
  }
  .plan--day { left: 66px; top: 526px; height: 330px; }
  .plan--all { left: 450px; top: 526px; height: 330px; }
  .plan--light { left: 258px; top: 501px; height: 357px; background: linear-gradient(180deg, #29a9e1, #2aa5de); }
  .plan-icon { position: absolute; left: 0; top: 14px; width: 100%; display: flex; justify-content: center; }
  .plan-title {
    position: absolute; left: 0; top: 51px; width: 100%; height: 22px; line-height: 22px;
    background: var(--blue); color: var(--white); text-align: center; font-weight: 700; font-size: 15.5px;
    white-space: nowrap;
  }
  .plan--light .plan-title { top: 59px; background: var(--blue-deep); }
  .plan-features {
    position: absolute; left: 20px; right: 3px; list-style: none; color: var(--ink);
    font-size: 8.8px; line-height: 10.8px; letter-spacing: -0.1px;
  }
  .plan--day .plan-features { top: 85px; }
  .plan--all .plan-features { top: 79px; }
  .plan--light .plan-features { top: 101px; color: var(--white); }
  .plan-features li { position: relative; padding-left: 9px; margin-bottom: 2.9px; }
  .plan-features li::before {
    content: ""; position: absolute; left: 0; top: 1.5px; width: 7.5px; height: 7.5px; border-radius: 50%;
    background: var(--orange);
  }
  .plan--light .plan-features li::before { background: var(--white); }
  .plan-features li::after {
    content: ""; position: absolute; left: 2px; top: 3px; width: 3px; height: 1.7px;
    border-left: 1.2px solid var(--white); border-bottom: 1.2px solid var(--white); transform: rotate(-45deg);
  }
  .plan--light .plan-features li::after { border-color: var(--blue); }
  .plan-features .note { font-size: 7.4px; line-height: 9.5px; display: block; white-space: nowrap; }
  .plan--light .plan-features .note { margin-top: 3px; }

  .price-band { position: absolute; background: var(--orange); color: var(--white); text-align: center; }
  .price-band--day { left: 57px; top: 774px; width: 187px; height: 64px; }
  .price-band--all { left: 441px; top: 774px; width: 187px; height: 64px; }
  .price-band--light { left: 249px; top: 764px; width: 187px; height: 74px; }
  .price { font-weight: 600; font-size: 21px; line-height: 1; padding-top: 14px; }
  .price-note { font-style: italic; font-size: 9px; margin-top: 4px; }
  .price-split { display: flex; justify-content: center; align-items: center; gap: 6px; padding-top: 9px; }
  .price-split .col { line-height: 1; }
  .price-split .amount { font-weight: 600; font-size: 21px; }
  .price-split .unit { font-size: 13px; margin-top: 1px; }
  .price-split .plus { font-size: 24px; font-weight: 600; }

  .contact {
    position: absolute; top: 890px; width: 263px; height: 32px;
    border: 1.5px solid var(--white); border-radius: 12px; transform: skewX(-8deg);
  }
  .contact--web { left: 67px; }
  .contact--mail { left: 346px; }
  .contact-inner {
    transform: skewX(8deg); display: flex; align-items: center; justify-content: center; gap: 7px;
    height: 100%; color: var(--white); font-size: 15px;
  }
</style>
</head>
<body>
  <main class="flyer">
    <div class="top-area" role="img" aria-label="Faint photo of a bright open-plan office"></div>
    <div class="dark-area" role="img" aria-label="Dark faded photo of a large workspace interior"></div>
    <div class="accent-band"></div>

    <div class="brand">TeaLantern</div>

    <div class="hero-frame" role="img" aria-label="Photo of a white electric car plugged in with an orange charging cable"></div>

    <h1 class="headline">Flexible Workspace with</h1>
    <div class="headline-accent">EV CHARGING</div>

    <section class="plan plan--day">
      <div class="plan-icon">
        <svg width="30" height="24" viewBox="0 0 30 24" fill="none" stroke="#29a9e1" stroke-width="1.5"><rect x="1" y="5" width="28" height="18" rx="1"/><path d="M10 5V2h10v3M1 8l14 7 14-7"/></svg>
      </div>
      <h2 class="plan-title">Day Member</h2>
      <ul class="plan-features">
        <li>Use of Hot Desks &amp; Lounge Areas</li>
        <li>Secure Wifi</li>
        <li>Free Tea &amp; Coffee</li>
      </ul>
    </section>

    <section class="plan plan--light">
      <div class="plan-icon">
        <svg width="36" height="36" viewBox="0 0 36 36" fill="none" stroke="#ffffff" stroke-width="1.5"><circle cx="13" cy="23" r="11"/><circle cx="13" cy="23" r="6"/><circle cx="13" cy="23" r="1.5"/><path d="M13 23L31 5M26 5h5v5M28 2l3 3"/></svg>
      </div>
      <h2 class="plan-title">Light Member</h2>
      <ul class="plan-features">
        <li>Use of Hot Desks &amp; Lounge Areas</li>
        <li>Secure Wifi</li>
        <li>Free Tea &amp; Coffee</li>
        <li>Discounted E/V Charge Rates</li>
        <li>Access to Meeting Rooms<span class="note">(£10+vat per person, per hour)</span></li>
      </ul>
    </section>

    <section class="plan plan--all">
      <div class="plan-icon">
        <svg width="36" height="26" viewBox="0 0 36 26" fill="none" stroke="#29a9e1" stroke-width="1.5"><path d="M8 1h20l7 8-17 16L1 9z M1 9h34 M13 1l-4 8 9 16 9-16-4-8 M18 1l-5 8M18 1l5 8"/></svg>
      </div>
      <h2 class="plan-title">All Access Member</h2>
      <ul class="plan-features">
        <li>Unlimited Number of Visits Each Month</li>
        <li>Dedicated Desk<span class="note">(lockable draws + £60 a month)</span></li>
        <li>Receptionist to Meet &amp; Greet Guests</li>
        <li>Use of Lounge Areas</li>
        <li>Secure Wifi</li>
        <li>Free Tea &amp; Coffee</li>
        <li>Discounted E/V Charge Rates</li>
        <li>Access to Meeting Rooms<span class="note">(£10+vat per person, per hour)</span></li>
      </ul>
    </section>

    <div class="price-band price-band--day">
      <div class="price">£18.00</div>
      <div class="price-note">Price Inclusive of VAT Per month</div>
    </div>
    <div class="price-band price-band--light">
      <div class="price-split">
        <div class="col"><div class="amount">£18.00</div><div class="unit">a month</div></div>
        <div class="plus">+</div>
        <div class="col"><div class="amount">£18.00</div><div class="unit">Each Visit</div></div>
      </div>
      <div class="price-note">Price Inclusive of VAT Per month</div>
    </div>
    <div class="price-band price-band--all">
      <div class="price">£18.00</div>
      <div class="price-note">Price Inclusive of VAT Per month</div>
    </div>

    <div class="contact contact--web">
      <div class="contact-inner">
        <svg width="16" height="16" viewBox="0 0 16 16" fill="none" stroke="#f39021" stroke-width="1.2"><circle cx="8" cy="8" r="7"/><ellipse cx="8" cy="8" rx="3" ry="7"/><path d="M1 8h14M2 4.5h12M2 11.5h12"/></svg>
        <span>www.tealantern.co.uk</span>
      </div>
    </div>
    <div class="contact contact--mail">
      <div class="contact-inner">
        <svg width="16" height="16" viewBox="0 0 16 16" fill="none" stroke="#f39021" stroke-width="1.2"><circle cx="8" cy="8" r="7"/><ellipse cx="8" cy="8" rx="3" ry="7"/><path d="M1 8h14M2 4.5h12M2 11.5h12"/></svg>
        <span>info@tealantern.co.uk</span>
      </div>
    </div>
  </main>
</body>
</html>
```